Dietitian needs awesome business card

I need a contemporary design that's eye catching but professional.
My card is to given to doctors, specialists and patients alike.
I manage patients with chronic diseases
I have uploaded my logo and current business card, I would also like the other Certified Clinical Nutritionist logo incorporated into the design

Target Market(s)

Doctors, specialists and patients

Industry/Entity Type

Healthcare

Contact Information for Business Card

www.brightfieldnutrition.com.au
Ph: 0427 561 903
Fax: 6457 2183
email: marcus.k.diet@fernmail.com
Space on the back of the card with: Appointment date, Appointment time and appointment location

Font styles to use
Serif

Colors
fbee3e
876aae
ffc214

Requirements
Must have
• My Logo
• Certified Clinical Nutritionist Logo
• My 4 locations - Pinebrook Medical Centre, North Corrin Health, Hollis Medical, Ashcombe Doctors Surgery
Nice to have
• I like the colours in my current business card

```html
<!DOCTYPE html>
<html lang="en">
<head>
<meta charset="utf-8">
<title>Brightfield Nutrition &amp; Dietetics – Business Card</title>
<link rel="stylesheet" href="https://fonts.googleapis.com/css2?family=Archivo+Narrow:wght@400;600&family=Overpass:wght@600;700&display=swap">
<style>
  :root {
    --backdrop: #3b3431;
    --card: #1d1d1e;
    --card-edge: #2a2a2c;
    --ink: #e9e9ea;
    --rule: #8d8d92;
    --brand-blue: #2f55b8;
    --brand-green: #8cc63f;
    --badge-orange: #f47b20;
    --white: #ffffff;
  }
  * { box-sizing: border-box; margin: 0; padding: 0; }
  html, body { width: 1200px; height: 787px; overflow: hidden; }
  body {
    background: var(--backdrop);
    font-family: "Archivo Narrow", "Arial Narrow", sans-serif;
    color: var(--ink);
    display: flex;
    align-items: center;
    justify-content: center;
    gap: 50px;
  }
  .card {
    position: relative;
    width: 540px;
    height: 330px;
    background: var(--card);
    border: 1px solid var(--card-edge);
    border-radius: 4px;
    box-shadow: 0 10px 24px rgba(0,0,0,.45);
  }

  /* ---------- appointment side ---------- */
  .brand {
    position: absolute;
    top: 22px; left: 28px;
    display: flex; align-items: center; gap: 10px;
  }
  .brand-dot {
    width: 34px; height: 34px; border-radius: 50%;
    background: var(--brand-blue);
  }
  .brand-name {
    font-family: "Archivo Narrow", sans-serif;
    font-weight: 600;
    font-size: 17px;
    line-height: 1.05;
    color: var(--brand-blue);
  }
  .write-line {
    position: absolute;
    left: 28px;
    height: 1px;
    background: var(--rule);
  }
  .field-label {
    position: absolute;
    font-size: 15px;
    color: var(--brand-blue);
  }
  .ampm {
    position: absolute;
    font-size: 12px;
    color: var(--brand-blue);
  }
  .locations {
    position: absolute;
    list-style: none;
    font-size: 14px;
    color: var(--ink);
  }
  .locations li {
    display: flex; align-items: center; gap: 8px;
    margin-bottom: 6px;
  }
  .locations li::before {
    content: "";
    width: 11px; height: 11px;
    border: 1px solid var(--ink);
  }
  .cert-badge {
    position: absolute;
    top: 70px; right: 30px;
    width: 138px; height: 62px;
    background: var(--badge-orange);
    display: flex; align-items: center; justify-content: space-between;
    padding: 0 10px;
  }
  .cert-badge-text {
    font-size: 11px; line-height: 1.2; color: var(--white);
  }
  .cert-badge-mark {
    width: 38px; height: 38px; border-radius: 50%;
    background: var(--white);
  }

  /* ---------- contact side ---------- */
  .logo-mark {
    position: absolute;
    top: 92px; left: 62px;
    width: 140px; height: 140px;
    display: flex; align-items: center; justify-content: center;
  }
  .logo-mark-dot {
    width: 120px; height: 120px; border-radius: 50%;
    background: var(--brand-green);
  }
  .divider {
    position: absolute;
    top: 80px; left: 238px;
    width: 1px; height: 170px;
    background: linear-gradient(var(--card), var(--rule), var(--card));
  }
  .contact {
    position: absolute;
    top: 92px; left: 256px;
  }
  .person-name {
    font-family: "Overpass", sans-serif;
    font-weight: 700;
    font-size: 22px;
    color: var(--brand-blue);
    letter-spacing: .3px;
  }
  .person-role {
    font-family: "Overpass", sans-serif;
    font-weight: 700;
    font-size: 16px;
    color: var(--brand-green);
    margin-bottom: 8px;
  }
  .contact-list { list-style: none; font-size: 16px; }
  .contact-list li {
    display: flex; align-items: center; gap: 8px;
    line-height: 24px;
  }
  .contact-list svg { width: 14px; height: 14px; fill: var(--brand-blue); flex: none; }
</style>
</head>
<body>

  <section class="card card-appointment" aria-label="Appointment side">
    <div class="brand">
      <span class="brand-dot"></span>
      <span class="brand-name">Brightfield<br>Nutrition &amp; Dietetics</span>
    </div>

    <div class="cert-badge">
      <span class="cert-badge-text">Certified<br>Clinical<br>Nutritionist</span>
      <span class="cert-badge-mark"></span>
    </div>

    <span class="write-line" style="top:78px; width:320px;"></span>
    <span class="write-line" style="top:112px; width:320px;"></span>

    <span class="field-label" style="top:135px; left:28px;">Date :</span>
    <span class="write-line" style="top:153px; left:76px; width:272px;"></span>

    <span class="field-label" style="top:172px; left:214px;">Time :</span>
    <span class="write-line" style="top:190px; left:262px; width:200px;"></span>
    <span class="ampm" style="top:178px; left:470px;">AM/PM</span>

    <ul class="locations" style="top:222px; left:28px;">
      <li>Pinebrook Medical Centre</li>
      <li>North Corrin Health</li>
    </ul>
    <ul class="locations" style="top:222px; left:262px;">
      <li>Ashcombe Doctors Surgery</li>
      <li>Hollis Medical</li>
    </ul>
  </section>

  <section class="card card-contact" aria-label="Contact side">
    <div class="logo-mark">
      <span class="logo-mark-dot"></span>
    </div>
    <span class="divider"></span>

    <div class="contact">
      <h1 class="person-name">Marcus Kellaway</h1>
      <p class="person-role">Nutritionist &amp; Chef</p>
      <ul class="contact-list">
        <li>
          <svg viewBox="0 0 16 16" aria-hidden="true"><path d="M3 1h3l1.5 4-2 1.3a9 9 0 0 0 4.2 4.2L11 8.5l4 1.5v3a2 2 0 0 1-2 2A12 12 0 0 1 1 3a2 2 0 0 1 2-2z"/></svg>
          0427 561 903
        </li>
        <li>
          <svg viewBox="0 0 16 16" aria-hidden="true"><path d="M4 1h7v4H4zM1 6h14v7h-3v2H4v-2H1zm4 5v3h6v-3z"/></svg>
          6457 2183
        </li>
        <li>
          <svg viewBox="0 0 16 16" aria-hidden="true"><path d="M1 3h14v10H1zm1.5 1.2L8 8.5l5.5-4.3z"/></svg>
          marcus.k.diet@fernmail.com
        </li>
        <li>
          <svg viewBox="0 0 16 16" aria-hidden="true"><circle cx="8" cy="8" r="7"/></svg>
          www.brightfieldnutrition.com.au
        </li>
      </ul>
    </div>
  </section>

</body>
</html>
```